US Recruiting Firm Needs Dynamic Tri-Fold Brochure

Need tri-fold professional brochure for HR recruiting and consulting firm based in the US.

Target Market(s)

Clients seeking administrative and human resources talent

Industry/Entity Type

Recruitment

Font styles to use
Sans Serif

Requirements
Should not have
• No weird shapes
• No heavy geometric shapes -- I prefer curvy lines
• Not a dark brochure

```html
<!DOCTYPE html>
<html lang="en">
<head>
<meta charset="utf-8">
<title>Harbor Lane Recruiters – Tri-Fold Brochure</title>
<link rel="stylesheet" href="https://fonts.googleapis.com/css2?family=Josefin+Sans:wght@400;600&family=Montserrat:wght@400;600;700;800&display=swap">
<style>
  :root{
    --navy:#123f5e;
    --navy-deep:#0d3350;
    --orange:#f26a0f;
    --green:#8dc63f;
    --magenta:#b83a8c;
    --ink:#2c2c2c;
    --paper:#ffffff;
    --stage:#e9ebee;
  }
  *{box-sizing:border-box;margin:0;padding:0}
  html,body{width:1200px;height:800px;overflow:hidden;background:var(--stage)}
  .brochure{position:absolute;left:60px;top:20px;width:1080px;height:760px;display:flex;box-shadow:0 6px 24px rgba(0,0,0,.18)}
  .panel{position:relative;width:360px;height:760px;background:var(--paper);overflow:hidden}
  .panel + .panel{border-left:1px solid #e3e3e3}

  .wave-band{position:absolute;left:0;bottom:0;width:360px;height:120px}
  .band-url{position:absolute;left:0;right:0;bottom:26px;text-align:center;color:#fff;
    font:600 17px/1 "Montserrat",sans-serif;letter-spacing:.5px}

  /* About panel */
  .about{position:relative;z-index:1;padding:48px 40px 0 40px}
  .about-title{font:400 26px/1 "Josefin Sans",sans-serif;color:var(--navy);letter-spacing:.5px}
  .about-title span{color:var(--orange);font-weight:600}
  .about-rule{display:block;width:240px;height:14px;margin:4px 0 14px}
  .about-copy{font:400 11.5px/1.5 "Josefin Sans",sans-serif;color:var(--ink);text-align:justify;margin-bottom:10px}
  .about-photo{position:absolute;left:0;top:500px;width:360px;height:180px;
    background:linear-gradient(160deg,#eef1f4 0%,#cfd6dd 55%,#9aa6b1 100%)}

  /* Middle panel */
  .team-photo{position:absolute;left:0;top:0;width:360px;height:520px;
    background:linear-gradient(180deg,#eef2f5 0%,#d4dce3 45%,#7c8a97 100%)}
  .cta-box{position:absolute;left:20px;top:400px;width:320px;height:190px;background:var(--orange);
    padding:24px 24px;color:#fff}
  .cta-lead{font:800 22px/1.1 "Montserrat",sans-serif;letter-spacing:.5px}
  .cta-small{font:400 13px/1.3 "Josefin Sans",sans-serif;letter-spacing:.5px;text-transform:uppercase}
  .cta-strong{font:800 16px/1.2 "Montserrat",sans-serif;letter-spacing:.5px}
  .cta-phone{font:800 18px/1 "Montserrat",sans-serif;margin-top:14px;letter-spacing:.8px}
  .cta-mail{font:400 13px/1 "Josefin Sans",sans-serif;margin-top:8px}

  /* Cover panel */
  .brand{position:absolute;left:28px;top:34px;display:flex;align-items:center;gap:10px}
  .brand-dot{width:34px;height:34px;border-radius:50%;background:var(--orange)}
  .brand-name{font:700 19px/1.05 "Montserrat",sans-serif;color:var(--navy);text-transform:uppercase}
  .brand-tag{font:400 10.5px/1 "Josefin Sans",sans-serif;color:var(--navy);margin-top:4px}
  .cover-photo{position:absolute;left:0;top:100px;width:360px;height:400px;
    background:linear-gradient(180deg,#f1f3f5 0%,#c9d1d8 50%,#5a6876 100%)}
  .focus-box{position:absolute;left:30px;top:420px;width:300px;height:200px;background:var(--navy-deep);
    padding:26px 24px;font-family:"Montserrat",sans-serif}
  .focus-label{color:var(--orange);font-weight:800;font-size:21px;letter-spacing:.5px}
  .focus-list{color:#fff;font:400 17px/1.3 "Josefin Sans",sans-serif;text-transform:uppercase;margin-top:8px}
  .focus-list strong{color:var(--green);font:800 19px/1.2 "Montserrat",sans-serif}
</style>
</head>
<body>
<main class="brochure">

  <section class="panel panel-about">
    <div class="about-photo" role="img" aria-label="Photo of a presenter leading a meeting at a whiteboard with colleagues seated at a table"></div>
    <div class="about">
      <h2 class="about-title">ABOUT <span>US</span></h2>
      <svg class="about-rule" viewBox="0 0 240 14" aria-hidden="true"><path d="M0 12 Q120 10 240 2" stroke="var(--magenta)" stroke-width="2" fill="none"/></svg>
      <p class="about-copy">Harbor Lane Recruiters is a recruiting and search firm that specializes in providing top-notch administrative, professional, and executive level human resources talent. We provide best-in-class talent to companies seeking to simplify their recruiting process, increase efficiency and optimize productivity. Each search is customized based on our client's requirements. We provide quality, timely, and efficient services. Our recruiters are highly skilled in identifying, screening, interviewing, and assessing candidates across various industries. We develop a partnership with our client and candidate in order to make the recruitment process a success for both parties.</p>
      <p class="about-copy">At Harbor Lane Recruiters, competence + talent emerge. We are experienced human resources professionals exclusively dedicated to recruiting and placing human resources professionals. We do we love and know for sure: human resources recruiting and consulting. We help awesome companies attract and retain the best employees, increase their profits, and optimize productivity.</p>
    </div>
    <svg class="wave-band" viewBox="0 0 360 120" preserveAspectRatio="none" aria-hidden="true">
      <path d="M0 30 Q180 -10 360 10 L360 120 L0 120 Z" fill="#fff"/>
      <path d="M0 42 Q180 2 360 22" stroke="var(--green)" stroke-width="3" fill="none"/>
      <path d="M0 48 Q180 8 360 28 L360 120 L0 120 Z" fill="var(--navy)"/>
    </svg>
    <div class="band-url">www.harborlanerecruit.com</div>
  </section>

  <section class="panel panel-contact">
    <div class="team-photo" role="img" aria-label="Photo of business professionals talking in a bright glass-walled office"></div>
    <div class="cta-box">
      <p class="cta-lead">TO LEARN MORE</p>
      <p class="cta-small">and request a</p>
      <p class="cta-strong">FREE CONSULTATION</p>
      <p class="cta-small">contact us today</p>
      <p class="cta-phone">CALL - 555 018 2040</p>
      <p class="cta-mail">info@harborlanerecruit.com</p>
    </div>
    <svg class="wave-band" viewBox="0 0 360 120" preserveAspectRatio="none" aria-hidden="true">
      <path d="M0 30 Q180 -10 360 10 L360 120 L0 120 Z" fill="#fff"/>
      <path d="M0 42 Q180 2 360 22" stroke="var(--green)" stroke-width="3" fill="none"/>
      <path d="M0 48 Q180 8 360 28 L360 120 L0 120 Z" fill="var(--navy)"/>
    </svg>
    <div class="band-url">www.harborlanerecruit.com</div>
  </section>

  <section class="panel panel-cover">
    <div class="cover-photo" role="img" aria-label="Photo of silhouetted business people standing in a sunlit office"></div>
    <div class="brand">
      <span class="brand-dot"></span>
      <div>
        <p class="brand-name">Harbor Lane<br>Recruiters</p>
        <p class="brand-tag">Human Resources Staffing &amp; Consulting</p>
      </div>
    </div>
    <div class="focus-box">
      <p class="focus-label">SPECIALIZING IN</p>
      <p class="focus-list">Administrative,<br>Professional,<br>and <strong>EXECUTIVE<br>HR TALENT</strong></p>
    </div>
    <svg class="wave-band" viewBox="0 0 360 120" preserveAspectRatio="none" aria-hidden="true">
      <path d="M0 30 Q180 -10 360 10 L360 120 L0 120 Z" fill="#fff"/>
      <path d="M0 42 Q180 2 360 22" stroke="var(--green)" stroke-width="3" fill="none"/>
      <path d="M0 48 Q180 8 360 28 L360 120 L0 120 Z" fill="var(--navy)"/>
    </svg>
    <div class="band-url">www.harborlanerecruit.com</div>
  </section>

</main>
</body>
</html>
```